Dara's Riverbend - a history of an interesting place

I need a book cover for a project on the history of a province in Cambodia. It is a joint project with Dara, who is a wheelchair bound local resident from the salt fields. This is a 200 year story told through the lives of his family and ancestors. The photo of the people should be on the back cover. The overall effect should be a historical book which draws people in with the detail of the two main images - map and drawing with the helicopter somewhere - maybe back cover? The title should not obscure the detail in the pictures too much.

Target Market(s)

Visitors to Kampot who are interested in the place

Font styles to use
Serif

Colors

Requirements
Must have
• A feel for the past (eg the French colonial map)
Nice to have
• Images of salt fields - the top left part of the drawing has this connection.
Should not have
• I want to avoid the image and perception of war - the helicopter may give a wrong impression - it was dropping food to starving villagers. Perhaps emphasize the map more?

```html
<!DOCTYPE html>
<html lang="en">
<head>
<meta charset="utf-8">
<title>Dara's Riverbend – Book Cover</title>
<link href="https://fonts.googleapis.com/css2?family=Playfair+Display:wght@700;900&family=Source+Serif+4:wght@300;400;600&display=swap" rel="stylesheet">
<style>
  :root {
    --teal: #1591b0;
    --spine: #1896b8;
    --sky-light: #bfe3f0;
    --sky-mid: #6fc0dc;
    --sky-deep: #3a9fc4;
    --paper: #ffffff;
    --ink: #1f2328;
    --ink-soft: #5a5f66;
    --backdrop: #9b9ea2;
  }
  * { margin: 0; padding: 0; box-sizing: border-box; }
  html, body { width: 1200px; height: 1200px; overflow: hidden; }
  body {
    background: var(--backdrop);
    font-family: "Source Serif 4", serif;
    display: flex; align-items: center; justify-content: center;
  }
  .book-spread {
    width: 1112px; height: 762px;
    display: flex; background: var(--paper);
    box-shadow: 0 10px 30px rgba(0,0,0,.18);
  }

  /* Back cover */
  .back-cover { position: relative; width: 510px; height: 100%; background: var(--paper); }
  .back-cover__sky {
    position: absolute; left: 0; top: 0; width: 100%; height: 375px;
    background: linear-gradient(180deg, var(--sky-deep) 0%, var(--sky-mid) 45%, var(--sky-light) 100%);
  }
  .back-cover__photo {
    position: absolute; left: 40px; top: 165px; width: 420px; height: 312px;
    background: var(--paper); padding: 6px;
    box-shadow: 0 1px 4px rgba(0,0,0,.25);
  }
  .back-cover__photo div {
    width: 100%; height: 100%;
    background: linear-gradient(180deg, #e9eef0 0%, #b8c9a6 30%, #6f8f5a 45%, #8fb3c0 60%, #5a7a84 100%);
  }
  .blurb { position: absolute; left: 46px; top: 494px; width: 420px; color: var(--ink-soft); }
  .blurb__lead { font-size: 10.5px; font-weight: 600; color: var(--ink); line-height: 1.3; margin-bottom: 9px; }
  .blurb p { font-size: 9.4px; font-weight: 300; line-height: 1.34; text-align: justify; margin-bottom: 6px; }
  .blurb p.blurb__lead { font-size: 10.5px; font-weight: 600; text-align: left; }

  /* Spine */
  .spine {
    width: 92px; height: 100%; background: var(--spine);
    display: flex; flex-direction: column; align-items: center;
    padding: 40px 0 40px; color: var(--paper);
  }
  .spine__title {
    writing-mode: vertical-rl; font-family: "Playfair Display", serif; font-weight: 900;
    font-size: 38px; line-height: 1; white-space: nowrap;
  }
  .spine__authors {
    margin-top: auto; writing-mode: vertical-rl; font-weight: 600;
    font-size: 15px; line-height: 1.15; white-space: nowrap; letter-spacing: .6px;
  }

  /* Front cover */
  .front-cover { position: relative; width: 510px; height: 100%; background: var(--paper); }
  .front-cover__title {
    position: absolute; top: 34px; left: 0; width: 100%;
    text-align: center; color: var(--teal);
    font-family: "Playfair Display", serif; font-weight: 900; line-height: .92;
  }
  .front-cover__title .line-1 { display: block; font-size: 90px; }
  .front-cover__title .line-2 { display: block; font-size: 58px; }
  .front-cover__map {
    position: absolute; left: 44px; top: 200px; width: 422px; height: 340px;
    border-radius: 6px;
    background:
      linear-gradient(180deg, #c9c6c0 0%, #9fb0ad 36%, #f0a01e 52%, #3a2a14 66%, #c98a22 86%, #e0a33a 100%);
  }
  .front-cover__strip {
    position: absolute; left: 44px; top: 560px; width: 422px; height: 108px;
    background: var(--paper); padding: 6px;
    box-shadow: 0 1px 4px rgba(0,0,0,.25);
  }
  .front-cover__strip div {
    width: 100%; height: 100%;
    background: linear-gradient(90deg, #c56a4e 0%, #6ab0d8 22%, #4a9fd4 45%, #2f6fb0 60%, #b8603e 78%, #9c4a34 100%);
  }
  .front-cover__authors {
    position: absolute; left: 0; top: 686px; width: 100%; text-align: center;
    color: var(--ink-soft); font-weight: 600; font-size: 19px; line-height: 1.05; letter-spacing: .6px;
  }
  .front-cover__authors small { display: block; font-size: 15px; }
</style>
</head>
<body>
  <main class="book-spread">
    <section class="back-cover">
      <div class="back-cover__sky" role="img" aria-label="Faded blue-toned old colonial map with an aircraft dropping supplies"></div>
      <figure class="back-cover__photo">
        <div role="img" aria-label="Photograph of three men talking beside a river, one seated in a wheelchair, hills behind"></div>
      </figure>
      <div class="blurb">
        <p class="blurb__lead">Dara's Riverbend – a modern history of the colourful Cambodian province of Kampot, told through the lives of the salt fields tribe of Chum Kriel.</p>
        <p>Just outside of Kampot town is the district of Chum Kriel, which contains hundreds of salt fields, fringed with small, basic houses and rice paddies. This book tells the stories of some of the resilient, resourceful and courageous people who have made their lives there.</p>
        <p>Based on both documentary research and individual interviews, Dara's Riverbend provides some answers to those who are curious about what the southern most edge of Cambodia has been through during the last 200 years. Kampot Province has been a land of bandits and pirates, insurrection and terrible brutality, pioneering agriculture and tribal enclaves, and colonialist endeavours and heroic resistance.</p>
        <p>In particular, the book follows the extended family of Dara Vanna through the twentieth century to the present, including the catastrophic 1970s, when civil war and the Khmer Rouge dominated the province.</p>
        <p>Kampot is being drawn rapidly into the technological new millennium but this book seeks to ensure its rich past is not forgotten.</p>
      </div>
    </section>

    <section class="spine">
      <h2 class="spine__title">DARA'S RIVERBEND</h2>
      <p class="spine__authors">TOM HADLEY<br>WITH DARA VANNA</p>
    </section>

    <section class="front-cover">
      <h1 class="front-cover__title">
        <span class="line-1">DARA'S</span>
        <span class="line-2">RIVERBEND</span>
      </h1>
      <div class="front-cover__map" role="img" aria-label="Province outline filled with an old colonial map, river greenery and a sunset over the water with a small boat"></div>
      <figure class="front-cover__strip">
        <div role="img" aria-label="Colourful hand-drawn picture of salt field workers carrying baskets beside blue water and brick buildings"></div>
      </figure>
      <p class="front-cover__authors">TOM HADLEY<small>WITH DARA VANNA</small></p>
    </section>
  </main>
</body>
</html>
```